MRT Property - Business Cards

Looking for a business card & general letterhead, signage etc design for our new logo.

Colours:
000a20
0056a2
00b5ef
0088ce
68cef2

Fonts:
Poppins
Karla

Please keep look and feel of new brand - example in the zip package I sent.

```html
<!DOCTYPE html>
<html lang="en">
<head>
<meta charset="utf-8">
<title>MRT Property – Business Cards</title>
<link rel="stylesheet" href="https://fonts.googleapis.com/css2?family=Poppins:wght@300;400;600;700&family=Karla:wght@400;500&display=swap">
<style>
  :root {
    --ink: #000a20;
    --navy-card: #12152b;
    --royal: #0056a2;
    --cyan: #00b5ef;
    --azure: #0088ce;
    --sky: #68cef2;
    --band: #1e98e0;
    --paper: #ffffff;
    --grey-text: #5c5f66;
    --stage: #e6e9ef;
  }
  * { box-sizing: border-box; margin: 0; padding: 0; }
  html, body { width: 1200px; height: 800px; overflow: hidden; }
  body {
    background: var(--stage);
    display: flex;
    align-items: center;
    justify-content: center;
    gap: 40px;
    font-family: "Poppins", sans-serif;
  }
  .card {
    position: relative;
    width: 540px;
    height: 309px;
    border-radius: 22px;
    overflow: hidden;
    box-shadow: 0 12px 30px rgba(0, 10, 32, 0.18);
  }

  /* Front */
  .card--front {
    background: var(--navy-card);
    display: flex;
    align-items: center;
    justify-content: center;
  }
  .brand {
    display: flex;
    align-items: center;
    gap: 14px;
  }
  .brand__dot {
    border-radius: 50%;
    background: var(--azure);
    flex: none;
  }
  .brand__name {
    font-family: "Poppins", sans-serif;
    font-weight: 600;
    white-space: nowrap;
  }
  .card--front .brand__dot { width: 40px; height: 40px; }
  .card--front .brand__name { font-size: 44px; color: var(--paper); }

  /* Back */
  .card--back { background: var(--paper); }
  .card__curves { position: absolute; inset: 0; }
  .card--back .brand { position: absolute; left: 30px; top: 42px; gap: 10px; }
  .card--back .brand__dot { width: 26px; height: 26px; }
  .card--back .brand__name { font-size: 28px; color: var(--royal); }

  .person { position: absolute; left: 250px; top: 118px; }
  .person__name {
    font-weight: 700;
    font-size: 21px;
    letter-spacing: 0.5px;
    color: var(--royal);
    text-transform: uppercase;
    line-height: 1.1;
  }
  .person__role {
    font-weight: 300;
    font-size: 15px;
    color: var(--sky);
    margin-top: 2px;
  }

  .contact {
    position: absolute;
    left: 30px;
    bottom: 26px;
    list-style: none;
    font-family: "Karla", sans-serif;
    font-size: 14px;
    color: var(--grey-text);
    line-height: 1.35;
  }
  .contact li { display: flex; align-items: center; gap: 8px; }
  .contact__icon { width: 13px; height: 13px; flex: none; fill: var(--royal); }
  .contact__spacer { width: 13px; flex: none; }
</style>
</head>
<body>
  <section class="card card--front" aria-label="Card front">
    <div class="brand">
      <span class="brand__dot"></span>
      <span class="brand__name">MRT Property</span>
    </div>
  </section>

  <section class="card card--back" aria-label="Card back">
    <svg class="card__curves" viewBox="0 0 540 309" aria-hidden="true">
      <path d="M290 0 H540 V309 H505 C488 165 420 55 290 0 Z" fill="var(--band)"/>
      <path d="M338 14 C430 48 488 150 497 309 H505 C488 165 420 55 338 14 Z" fill="var(--paper)"/>
      <path d="M352 20 C440 58 484 160 488 309 H497 C490 165 440 60 352 20 Z" fill="var(--sky)"/>
    </svg>

    <div class="brand">
      <span class="brand__dot"></span>
      <span class="brand__name">MRT Property</span>
    </div>

    <div class="person">
      <p class="person__name">Dalen Vorske</p>
      <p class="person__role">Managing Director</p>
    </div>

    <ul class="contact">
      <li>
        <svg class="contact__icon" viewBox="0 0 16 16" aria-hidden="true"><path d="M8 0a5.5 5.5 0 0 0-5.5 5.5C2.5 10 8 16 8 16s5.5-6 5.5-10.5A5.5 5.5 0 0 0 8 0Zm0 7.8a2.3 2.3 0 1 1 0-4.6 2.3 2.3 0 0 1 0 4.6Z"/></svg>
        187 W Harlow Ave
      </li>
      <li><span class="contact__spacer"></span>Fairmont, CA 90810</li>
      <li>
        <svg class="contact__icon" viewBox="0 0 16 16" aria-hidden="true"><path d="M3.6 1 6 3.9 4.7 5.6a9.5 9.5 0 0 0 5.7 5.7L12.1 10 15 12.4l-1.5 2.3C7.5 15.4.6 8.5 1.3 2.5Z"/></svg>
        (555) 214-3309
      </li>
      <li>
        <svg class="contact__icon" viewBox="0 0 16 16" aria-hidden="true"><path d="M1 3h14v10H1Zm1.5 1.2L8 8.6l5.5-4.4Z"/></svg>
        info@mrtproperty.com
      </li>
      <li>
        <svg class="contact__icon" viewBox="0 0 16 16" aria-hidden="true"><circle cx="8" cy="8" r="7"/></svg>
        www.mrtproperty.com
      </li>
    </ul>
  </section>
</body>
</html>
```